Plenko - Shoe Fitting App : Foot scanning app, 3D reconstruction and Fit recommandation.

We are a startup that has developed a 3D scanning App that compares the 3d reconstructed foot to the 3D Last (mould) of a shoe to find the best match and recommend a shoe size with a graphical representation of the fit on a reconstructed foot without texturing. The challenge of this app is to have a simple and intuitive onboarding of the user with clean and crisp ui and a simple tutorial for foot scanning. 3D representation of the fit is also key. What you see is what you feel is what we would like to achieve.

Target Market(s)

Sneaker Brands and athletic shoes brands

Industry/Entity Type

Footwear

Font styles to use
Other font styles liked:
• Oswald or Droid Serif

Colors
0094D4
00A9DD
6FCCEA
C7EBF8
E9F6FB

Requirements
Must have
• Simple intuitive UI to onboard the customer to scan his bare foot (please look at attached image on how to scan the foot). You must flip your phone so that the screen is facing your foot. Start at 40cm distance form the front of your foot and turn 360% slowly to capture the foot while you feel the aptic of the iPhone. That needs to be presented with a simple animation that the user can easily understand and skip if he is a returning customer and knows how to do that. the rest of the UI is to present the result of the scanned foot for the user to use to get his fit and size. The other must have is the final result screen. Where the user will a representation of the foot (snug, loose ) of different predefined areas of the foot so he can choose the fit that he likes and not necessarily the size that we suggest. Must match website design (https://www.plenko.example)
Nice to have
• An animation of the whole process (scan-compare 3d foot with 3d shoe last(or mould) and get the 3D result of the best fit + associated size. Optionaly, an option to play with your foot and transform it (avatar like with accessories and colours)
Should not have
• Too many colours. Too much text. No gender type. No race type.

```html
<!DOCTYPE html>
<html lang="en">
<head>
<meta charset="utf-8">
<title>Plenko – Shoe Fitting App Screens</title>
<link rel="stylesheet" href="https://fonts.googleapis.com/css2?family=Poppins:wght@300;400;500;600;700&display=swap">
<style>
  :root{
    --canvas:#c8c8c8;
    --screen:#1b1a1b;
    --teal:#4db6b6;
    --white:#ffffff;
    --ink:#111111;
    --ring-1:#6a6a6a;
    --ring-2:#8c8c8c;
    --ring-3:#b4b4b4;
    --grey-btn:#7a7a7a;
    --card-light:#f1f1f1;
    --fit-loose:#7fb6ff;
    --fit-neutral:#9be3a0;
    --fit-tight:#ff8a7a;
  }
  *{box-sizing:border-box;margin:0;padding:0}
  html,body{width:1200px;height:526px;overflow:hidden}
  body{background:var(--canvas);font-family:"Poppins",sans-serif;color:var(--white);position:relative}
  .screen{position:absolute;background:var(--screen);width:173px}
  .abs{position:absolute}
  .center-x{left:0;right:0;text-align:center}
  .brand{font-weight:700;font-size:17px;letter-spacing:1px;line-height:1}
  .headline{font-size:11.5px;line-height:15px;text-transform:uppercase;font-weight:400}
  .headline b{font-weight:700}
  .btn{position:absolute;height:25px;border-radius:13px;background:var(--teal);color:var(--white);font-weight:700;font-size:8.5px;display:flex;align-items:center;justify-content:center;gap:5px;text-transform:uppercase}
  .btn svg{width:9px;height:9px}
  .btn.dark{background:#000}
  .dots{position:absolute;top:0;left:0}
  .dot{position:absolute;border-radius:50%}
  .art{position:absolute;border-radius:50%;background:
      radial-gradient(ellipse 40% 55% at 52% 40%,#d2d2d2 0%,rgba(210,210,210,0) 100%),
      radial-gradient(ellipse 55% 25% at 50% 78%,#c4c4c4 0%,rgba(196,196,196,0) 100%),
      radial-gradient(circle at 50% 45%,#ffffff 0%,#ececec 75%,#d6d6d6 100%)}
  .art.fit{background:
      radial-gradient(ellipse 35% 30% at 35% 75%,var(--fit-tight) 0%,rgba(255,138,122,0) 100%),
      radial-gradient(ellipse 30% 35% at 62% 55%,var(--fit-neutral) 0%,rgba(155,227,160,0) 100%),
      radial-gradient(ellipse 25% 40% at 55% 22%,var(--fit-loose) 0%,rgba(127,182,255,0) 100%),
      radial-gradient(circle at 50% 45%,#ffffff 0%,#ececec 75%,#d6d6d6 100%)}
  .silhouette{position:absolute;background:linear-gradient(160deg,#2a2a2a,#0b0b0b);border-radius:45% 30% 35% 55%/40% 30% 45% 55%}
  .card{position:absolute;border-radius:5px}
  .small{font-size:5.3px;line-height:9px;font-weight:300}
  .tabs{position:absolute;display:flex;border:1px solid #555;border-radius:4px;overflow:hidden;font-size:5.8px;font-weight:600}
  .tabs span{flex:1;display:flex;align-items:center;justify-content:center}
  .tabs .on{background:var(--teal)}
  .pref{position:absolute;width:30px;height:30px;border-radius:50%;display:flex;align-items:center;justify-content:center;font-size:5.8px;font-weight:700;color:var(--white)}
</style>
</head>
<body>

<svg width="0" height="0" style="position:absolute">
  <defs>
    <symbol id="arrow" viewBox="0 0 12 12"><path d="M1 6h9M6.5 2.5 10 6l-3.5 3.5" fill="none" stroke="currentColor" stroke-width="1.8" stroke-linecap="round" stroke-linejoin="round"/></symbol>
  </defs>
</svg>

<!-- Screen 1: lighting -->
<section class="screen" style="left:28px;top:50px;height:352px">
  <div class="abs center-x brand" style="top:28px">PLENKO</div>
  <h2 class="abs center-x headline" style="top:60px">Make sure your’re in<br><b>a well lit area</b></h2>
  <svg class="abs" style="left:9px;top:99px" width="159" height="159" viewBox="0 0 159 159">
    <circle cx="79.5" cy="79.5" r="79" fill="var(--ring-1)"/>
    <circle cx="79.5" cy="79.5" r="70" fill="var(--ring-2)"/>
    <circle cx="79.5" cy="79.5" r="60" fill="var(--ring-3)"/>
  </svg>
  <div class="art" role="img" aria-label="Line illustration of a glowing light bulb" style="left:37px;top:127px;width:103px;height:103px"></div>
  <div class="btn" style="left:17px;top:269px;width:140px">Next <svg><use href="#arrow"/></svg></div>
  <div class="dots">
    <span class="dot" style="left:42px;top:319px;width:10px;height:10px;background:#fff"></span>
    <span class="dot" style="left:64px;top:313px;width:9px;height:9px;background:#2c2c2c"></span>
    <span class="dot" style="left:85px;top:313px;width:9px;height:9px;background:#cfcfcf"></span>
    <span class="dot" style="left:106px;top:313px;width:9px;height:9px;background:#cfcfcf"></span>
  </div>
</section>

<!-- Screen 2: bare foot -->
<section class="screen" style="left:221px;top:50px;height:352px">
  <div class="abs center-x brand" style="top:28px">PLENKO</div>
  <h2 class="abs center-x headline" style="top:60px">Take off your shoes<br><b>and roll up pants</b></h2>
  <svg class="abs" style="left:20px;top:106px" width="138" height="138" viewBox="0 0 138 138">
    <circle cx="69" cy="69" r="69" fill="var(--ring-1)"/>
  </svg>
  <div class="art" role="img" aria-label="Wireframe illustration of a bare foot with a sneaker beside it" style="left:30px;top:116px;width:118px;height:118px"></div>
  <div class="btn" style="left:17px;top:269px;width:140px">Next <svg><use href="#arrow"/></svg></div>
  <div class="dots">
    <span class="dot" style="left:60px;top:316px;width:9px;height:9px;background:#cfcfcf"></span>
    <span class="dot" style="left:78px;top:316px;width:9px;height:9px;background:#2c2c2c"></span>
    <span class="dot" style="left:100px;top:316px;width:9px;height:9px;background:#cfcfcf"></span>
  </div>
</section>

<!-- Screen 3: scanning instruction -->
<section class="screen" style="left:411px;top:50px;height:352px">
  <div class="abs center-x brand" style="top:28px">PLENKO</div>
  <h2 class="abs center-x headline" style="top:60px">Flip the screen<br><b>toward your toes to<br>start scanning</b></h2>
  <div class="silhouette" role="img" aria-label="Dotted silhouette of a foot seen from the side" style="left:12px;top:116px;width:158px;height:130px"></div>
  <svg class="abs" style="left:74px;top:248px" width="26" height="17" viewBox="0 0 26 17">
    <text x="13" y="10" text-anchor="middle" font-family="Poppins,sans-serif" font-size="8" font-weight="700" fill="#fff">360°</text>
    <path d="M3 9c0 4 4.5 6 10 6s10-2 10-6" fill="none" stroke="#fff" stroke-width="1"/>
    <path d="M21 14l2-1-1-2" fill="none" stroke="#fff" stroke-width="1"/>
  </svg>
  <p class="abs center-x" style="top:268px;font-size:8px;line-height:12px;font-weight:600">scanned at 40 cm distance<br>at a low speed</p>
  <div class="btn" style="left:17px;top:302px;width:140px">Right foot <svg><use href="#arrow"/></svg></div>
</section>

<!-- Screen 4: reconstruction check -->
<section class="screen" style="left:617px;top:48px;height:352px">
  <div class="abs center-x brand" style="top:29px">PLENKO</div>
  <p class="abs center-x" style="top:61px;font-size:7.3px;line-height:12px;font-weight:600">Please check that the reconstruction<br>of your foot sems correct.</p>
  <svg class="abs" style="left:15px;top:93px" width="148" height="148" viewBox="0 0 148 148">
    <circle cx="74" cy="74" r="73" fill="none" stroke="var(--teal)" stroke-width="0.8"/>
    <circle cx="74" cy="74" r="69" fill="var(--ring-1)"/>
    <circle cx="74" cy="74" r="60" fill="var(--ring-2)"/>
  </svg>
  <div class="art" role="img" aria-label="Wireframe 3D reconstruction of the scanned foot" style="left:38px;top:116px;width:102px;height:102px"></div>
  <svg class="abs" style="left:77px;top:246px" width="25" height="17" viewBox="0 0 25 17">
    <path d="M1.5 8.5C5 3 9 1.5 12.5 1.5S20 3 23.5 8.5C20 14 16 15.5 12.5 15.5S5 14 1.5 8.5z" fill="none" stroke="var(--teal)" stroke-width="1.6"/>
    <circle cx="12.5" cy="8.5" r="3.6" fill="none" stroke="var(--teal)" stroke-width="1.6"/>
  </svg>
  <div class="btn dark" style="left:18px;top:274px;width:140px">Scan again <svg><use href="#arrow"/></svg></div>
  <div class="btn" style="left:18px;top:303px;width:140px">My fit <svg><use href="#arrow"/></svg></div>
</section>

<!-- Screen 5: measured & preferences -->
<section class="screen" style="left:811px;top:48px;height:432px">
  <div class="abs center-x brand" style="top:18px">PLENKO</div>
  <div class="card" style="left:18px;top:53px;width:140px;height:78px;background:#000;border:1px solid #555">
    <h2 class="abs center-x headline" style="top:8px">Your’re all<br><b>measured up</b></h2>
    <p class="abs center-x" style="top:47px;font-size:6.5px;font-weight:700">100%</p>
    <span class="abs" style="left:11px;top:60px;width:118px;height:3px;background:var(--teal);border-radius:2px"></span>
  </div>
  <div class="card" style="left:18px;top:144px;width:139px;height:127px;background:var(--white);color:var(--ink);border:1px solid #888">
    <h3 class="abs" style="left:14px;top:12px;font-size:9.5px;line-height:10.5px;font-weight:400">FUN FACT<br><b style="font-weight:700">ABOUT FEET</b></h3>
    <div class="abs" role="img" aria-label="Small line drawing of a measuring tape" style="left:95px;top:11px;width:32px;height:27px;border-radius:6px;background:#e6e6e6"></div>
    <p class="abs small" style="left:14px;top:44px;width:120px;line-height:10px">Feet grow as we age - our arch may flatten causing our foot size to increase</p>
    <p class="abs small" style="left:14px;top:69px;width:110px">Click below to see how this shoe fits. Now that you’re scanned, you can quickly try other shoes without going through the process again</p>
  </div>
  <div class="btn" style="left:48px;top:261px;width:80px;height:21px;font-size:7px">See results</div>
  <div class="card" style="left:19px;top:290px;width:140px;height:127px;background:var(--card-light);color:var(--ink)">
    <h3 class="abs center-x headline" style="top:15px;font-size:10px;line-height:10.5px">Tell us your<br><b>preference</b></h3>
    <p class="abs center-x" style="top:39px;font-size:6.3px">How do you prfer the cushion?</p>
    <svg class="abs" style="left:9px;top:72px" width="6" height="8" viewBox="0 0 6 8"><path d="M5 1 1.5 4 5 7" fill="none" stroke="#111" stroke-width="1.3"/></svg>
    <span class="pref" style="left:17px;top:60px;background:var(--grey-btn)">SOFT</span>
    <span class="pref" style="left:55px;top:60px;background:#000">MEDIUM</span>
    <span class="pref" style="left:93px;top:60px;background:var(--teal)">HARD</span>
    <svg class="abs" style="left:128px;top:71px" width="6" height="8" viewBox="0 0 6 8"><path d="M1 1 4.5 4 1 7" fill="none" stroke="#111" stroke-width="1.3"/></svg>
    <p class="abs center-x small" style="top:96px;font-size:5.4px">Select an option to go to the next personal<br>preference setting</p>
  </div>
</section>

<!-- Screen 6: fit result -->
<section class="screen" style="left:997px;top:48px;height:352px">
  <div class="abs center-x brand" style="top:18px">PLENKO</div>
  <p class="abs center-x" style="top:48px;font-size:10.5px;font-weight:400">FITMATCH</p>
  <h2 class="abs center-x" style="top:67px;font-size:9.5px;font-weight:700">Your Ideal Size is 8</h2>
  <p class="abs center-x" style="top:83px;font-size:5.8px;font-weight:400">Click to see how each part of this shoe fits your foot</p>
  <div class="tabs" style="left:20px;top:101px;width:139px;height:17px">
    <span>HEEL</span><span class="on">MIDFOOT</span><span>FOREFOOT</span>
  </div>
  <svg class="abs" style="left:34px;top:125px" width="110" height="110" viewBox="0 0 110 110">
    <circle cx="55" cy="55" r="55" fill="var(--ring-1)"/>
    <circle cx="55" cy="55" r="48" fill="var(--ring-2)"/>
  </svg>
  <div class="art fit" role="img" aria-label="3D foot coloured by fit: loose zones in blue, neutral in green, tight zones in red" style="left:48px;top:139px;width:82px;height:82px"></div>
  <p class="abs" style="left:105px;top:240px;font-size:5.3px;font-weight:600">Your Score</p>
  <span class="abs" style="left:21px;top:252px;width:137px;height:6px;border-radius:3px;background:linear-gradient(90deg,#c400ff,#4b3bff,#00b7ff,#00e08a,#5ee000,#ffd000,#ff7a00,#ff1a1a)"></span>
  <span class="abs" style="left:118px;top:249px;width:2px;height:12px;background:var(--teal)"></span>
  <div class="abs" style="left:19px;top:264px;width:142px;display:flex;justify-content:space-between;font-size:6.2px;font-weight:500">
    <span>Roomy</span><span>Neutral</span><span>Snug</span>
  </div>
  <p class="abs center-x" style="top:291px;font-size:6.2px;line-height:9px;font-weight:400">The colours on your foot show you<br>which parts of this shoe are tight<br>(red) or loose (blue).</p>
  <p class="abs center-x" style="top:326px;font-size:6.3px;font-weight:700;color:var(--teal)">What your see is what you’ll feel</p>
</section>

</body>
</html>
```